Drone service provider needs a brilliant web design

I need a responsive web design for a new drone service company. Pelham Drone Solutions provides turnkey solutions to capture, process, and deliver actionable aerial data to customers. The design should communicate a professional company that is safe, legal and insured. I included our logo design and business card designs for reference.
*content to be supplied after design selected

Target Market(s)

We serve telecommunications, construction, government, utility infrastructure, insurance and other industries.

Industry/Entity Type

Industrial

Number of Pages Required

5+ page

Colors

Designer to choose colors to be used in the design.

Requirements
Must have
• The design should highlight professional services to include Inspections, Mapping, Consulting and Training. The site should include aerial images and video to compliment the services offered. The landing page must include following sections in order: HOME, SERVICES, ABOUT, DEMO REEL, CLIENTS, CONTACT FORM, and social media buttons (Facebook, LinkedIn, Twitter, YouTube, Instagram). Contact: 615-382-9041 info@pelhamdronesolutions-example.com Smyrna, TN
• Sitemap:
• 6 pages: Home, Inspections, Mapping, Training, Consulting, About
• HOME (Landing Page)
• • Header with logo and tab links (Home, Services, About, Contact)
• • 'CAPTURE. PROCESS. DELIVER.' tagline and 'CONTACT US' button displayed within aerial image of drone over city or construction site
• • Services section with icons, text and read more link to page
• • About section with photo and text with three icons for SAFE. LEGAL. INSURED.
• • Demo reel
• • Clients logos shown scrolling horizontally
• • Contact form
• • Footer with logo, phone, email, social media buttons
• SERVICES (4 different pages)
• • Inspections
• • Mapping
• • Consulting
• • Training
• ABOUT page
• • Company
• • Partners
• • Certifications & Associations
• • Careers
• CONTACT linked to bottom of landing page
• Would you like to receive the newsletter? Yes or No Drop-down list
Nice to have
• Photos of KVR Marlin or Corvex inspecting infrastructure, buildings, construction sites, etc. A photo of one or two pilots in vest and helmet. Free stock photos preferred but would purchase the right photo that's more relevant.
• website references:
• https://www.quillrotor-example.com/
• https://www.brentfieldworks-example.com/services
• https://www.tomaro-example.com/
• http://gantrymetric-example.com/
• http://lumbrook-example.com/
• http://fennotics-example.com/
• https://www.grebe-example.io/
Should not have
• not an aerial photography or videography service business, no blog or newsletter

```html
<!DOCTYPE html>
<html lang="en">
<head>
<meta charset="utf-8">
<title>Pelham Drone Solutions</title>
<link href="https://fonts.googleapis.com/css2?family=Cabin:wght@400;500;600&family=Roboto:wght@400;500&display=swap" rel="stylesheet">
<style>
:root{
  --blue:#1687c6;
  --blue-dark:#0f6fa6;
  --ink:#333a40;
  --muted:#5d6368;
  --line:#d6dadd;
  --white:#ffffff;
  --dark:#2a2d31;
  --sky-top:#7fa6cf;
  --sky-mid:#c7d8e8;
  --land:#6d7a5e;
}
*{box-sizing:border-box;margin:0;padding:0}
html,body{width:1200px;height:2456px;overflow:hidden;background:var(--white)}
body{position:relative;font-family:"Roboto",Arial,sans-serif;color:var(--ink)}
.abs{position:absolute}

/* hero */
.hero-photo{left:0;top:0;width:1200px;height:700px;
  background:linear-gradient(180deg,var(--sky-top) 0%,#a9c3dd 25%,var(--sky-mid) 45%,#9fb0bb 62%,var(--land) 78%,#55604a 100%)}
.nav{top:54px;font-size:16px;letter-spacing:.5px;color:var(--ink);text-transform:uppercase}
.nav a{color:inherit;text-decoration:none;margin-right:42px}
.nav a.is-active{color:var(--blue)}
.nav-left{left:78px}
.nav-right{right:36px}
.brand{left:0;width:1200px;top:46px;text-align:center;font-family:"Cabin",sans-serif;font-weight:600;font-size:28px;letter-spacing:1px;color:#222;text-transform:uppercase}
.slide-arrow{top:266px;width:52px;height:52px;border-radius:50%;background:rgba(80,90,100,.55);color:var(--white);font-size:26px;line-height:50px;text-align:center}
.slide-prev{left:13px}
.slide-next{right:12px}
.hero-title{left:79px;top:248px;font-family:"Cabin",sans-serif;font-weight:600;font-size:50px;color:#2b2e31}
.hero-text{left:79px;top:336px;width:460px;font-size:16px;line-height:29px;color:#2b2e31}

/* services */
.service-label{font-family:"Cabin",sans-serif;font-weight:600;font-size:24px;color:var(--white);text-align:center;width:240px}
.service-icon{width:134px;height:134px;border-radius:50%;background:var(--white);border:5px solid var(--blue);box-shadow:0 0 0 4px rgba(255,255,255,.85)}
.service-icon svg{position:absolute;left:33px;top:33px}

/* welcome */
.welcome-title{left:0;width:1200px;top:1216px;text-align:center;font-family:"Cabin",sans-serif;font-weight:600;font-size:40px;color:var(--white)}
.welcome-text{left:172px;width:856px;top:1288px;text-align:center;font-family:"Cabin",sans-serif;font-size:15.5px;line-height:25px;color:var(--white)}

/* testimonials */
.section-title{left:0;width:1200px;text-align:center;font-family:"Cabin",sans-serif;font-weight:500;font-size:40px;color:var(--blue)}
.quote{width:430px;font-size:15px;line-height:25px;color:var(--muted)}
.quote-mark{font-family:Georgia,serif;font-size:34px;color:#7b8186;line-height:1}
.avatar{width:60px;height:60px;border-radius:50%;border:3px solid var(--blue);background:linear-gradient(180deg,#c9ced3,#7e8791)}
.client-name{font-size:16px;color:var(--blue)}
.divider{left:600px;top:1547px;width:1px;height:136px;background:var(--line)}

/* call to action */
.cta-photo{left:0;top:1752px;width:1200px;height:262px;background:linear-gradient(180deg,#2b86c0 0%,#3b8fc3 45%,#4f8f8a 100%)}
.cta-title{left:0;width:1200px;top:1822px;text-align:center;font-family:"Cabin",sans-serif;font-weight:600;font-size:36px;color:var(--white)}
.cta-button{left:506px;top:1894px;width:188px;height:46px;border-radius:23px;background:var(--white);color:var(--blue);font-family:"Cabin",sans-serif;font-weight:600;font-size:19px;line-height:46px;text-align:center;letter-spacing:.5px}

/* contact */
.field{border:1px solid #b9bec2;background:var(--white);font-size:15px;color:#4a5055;padding:0 12px}
.field-name{left:221px;top:2136px;width:449px;height:42px;line-height:40px}
.field-email{left:221px;top:2189px;width:449px;height:42px;line-height:40px}
.field-message{left:221px;top:2241px;width:333px;height:103px;padding-top:10px}
.send{left:566px;top:2241px;width:104px;height:103px;background:var(--blue);color:var(--white);text-align:center;font-family:"Cabin",sans-serif;font-weight:600;font-size:19px;letter-spacing:1px}
.send svg{display:block;margin:28px auto 10px}
.info{left:722px;font-size:15px;line-height:25px;color:var(--muted)}
.info svg{position:absolute;left:0;top:4px}
.info span{display:block;margin-left:34px}
.footer{left:0;top:2393px;width:1200px;height:63px;background:var(--blue);color:var(--white);text-align:center;font-size:15px;line-height:63px}
</style>
</head>
<body>

<!-- Hero -->
<div class="abs hero-photo" role="img" aria-label="Aerial photo of a drone flying over a river valley under a cloudy sky"></div>
<nav class="abs nav nav-left"><a class="is-active" href="#">Home</a><a href="#">About</a></nav>
<div class="abs brand">Pelham Drone Solutions</div>
<nav class="abs nav nav-right"><a href="#">Services</a><a href="#">Contact</a></nav>
<div class="abs slide-arrow slide-prev">&laquo;</div>
<div class="abs slide-arrow slide-next">&raquo;</div>
<h1 class="abs hero-title">safe, legal and insured</h1>
<p class="abs hero-text">Lorem Ipsum is simply dummy text of the printing and typesetting industry. Lorem Ipsum has been the industry's standard dummy text ever since.</p>

<!-- Services band with curved edges -->
<svg class="abs" style="left:0;top:575px" width="1200" height="860" viewBox="0 575 1200 860" aria-hidden="true">
  <defs>
    <linearGradient id="meetingTone" x1="0" y1="0" x2="1" y2="0">
      <stop offset="0" stop-color="#2f3338"/>
      <stop offset=".5" stop-color="#3b4046"/>
      <stop offset="1" stop-color="#26292d"/>
    </linearGradient>
  </defs>
  <path d="M0 581 Q600 695 1200 581 L1200 1210 L0 1210 Z" fill="url(#meetingTone)" role="img" aria-label="Photo of a team meeting around a table"/>
  <path d="M0 1203 Q600 1049 1200 1203 L1200 1427 L0 1427 Z" fill="var(--blue)"/>
  <line x1="560" y1="700" x2="380" y2="760" stroke="#fff" stroke-width="6"/>
  <line x1="640" y1="700" x2="820" y2="760" stroke="#fff" stroke-width="6"/>
  <circle cx="599" cy="681" r="103" fill="var(--blue)" stroke="#fff" stroke-width="5"/>
  <circle cx="599" cy="681" r="92" fill="none" stroke="#fff" stroke-width="2"/>
  <circle cx="599" cy="681" r="70" fill="#2b95d0" role="img" aria-label="Photo of a white quadcopter drone"/>
</svg>

<div class="abs service-icon" style="left:252px;top:699px">
  <svg width="68" height="68" viewBox="0 0 68 68" fill="none" stroke="var(--blue)" stroke-width="3"><rect x="14" y="10" width="40" height="52" rx="3"/><rect x="25" y="5" width="18" height="10" rx="2" fill="#fff"/><path d="M22 27h6M32 27h14M22 38h6M32 38h14M22 49h6M32 49h14"/></svg>
</div>
<div class="abs service-icon" style="left:812px;top:699px">
  <svg width="68" height="68" viewBox="0 0 68 68" fill="none" stroke="var(--blue)" stroke-width="3"><rect x="24" y="14" width="38" height="34"/><path d="M34 38l10-10 6 6 8-10"/><circle cx="14" cy="26" r="6" fill="var(--blue)"/><path d="M4 58V42q0-6 6-6h10l8 6" fill="var(--blue)"/></svg>
</div>
<div class="abs service-icon" style="left:408px;top:871px">
  <svg width="68" height="68" viewBox="0 0 68 68" fill="none" stroke="var(--blue)" stroke-width="3"><path d="M34 40s-11-12-11-20a11 11 0 0122 0c0 8-11 20-11 20z"/><circle cx="34" cy="20" r="4"/><path d="M20 38H12L5 62h58l-7-24h-8"/><path d="M14 52l14 4 12-8 16 6"/></svg>
</div>
<div class="abs service-icon" style="left:650px;top:871px">
  <svg width="68" height="68" viewBox="0 0 68 68" fill="var(--blue)"><circle cx="34" cy="16" r="10"/><path d="M16 44q0-16 18-16t18 16z"/><rect x="14" y="40" width="40" height="16" rx="2"/><rect x="6" y="56" width="56" height="5" rx="2"/></svg>
</div>

<div class="abs service-label" style="left:194px;top:856px">Inspection</div>
<div class="abs service-label" style="left:764px;top:856px;font-size:20px">Training</div>
<div class="abs service-label" style="left:344px;top:1028px">Mapping</div>
<div class="abs service-label" style="left:614px;top:1028px">Consulting</div>

<!-- Welcome -->
<h2 class="abs welcome-title">Welcome visitor!</h2>
<p class="abs welcome-text">There are many variations of passages of Lorem Ipsum available, but the majority have suffered alteration in some form, by injected humour, or randomised words which don't look even slightly believable. If you are going to use a passage of Lorem Ipsum, you need to be sure there isn't anything embarrassing hidden in the middle of text.</p>

<!-- Testimonials -->
<h2 class="abs section-title" style="top:1466px">What Our Client Say</h2>
<div class="abs quote-mark" style="left:78px;top:1550px">&ldquo;</div>
<p class="abs quote" style="left:108px;top:1540px">Lorem Ipsum is simply dummy text of the printing and typesetting industry. Lorem Ipsum has been the industry's standard dummy text ever since the 1500s.</p>
<div class="abs quote-mark" style="left:432px;top:1596px">&rdquo;</div>
<div class="abs avatar" style="left:111px;top:1632px" role="img" aria-label="Portrait photo of a client"></div>
<div class="abs client-name" style="left:188px;top:1652px">- Client Name</div>

<div class="abs divider"></div>

<div class="abs quote-mark" style="left:640px;top:1550px">&ldquo;</div>
<p class="abs quote" style="left:670px;top:1540px">Lorem Ipsum is simply dummy text of the printing and typesetting industry. Lorem Ipsum has been the industry's standard dummy text ever since the 1500s.</p>
<div class="abs quote-mark" style="left:994px;top:1596px">&rdquo;</div>
<div class="abs avatar" style="left:676px;top:1632px" role="img" aria-label="Portrait photo of a client"></div>
<div class="abs client-name" style="left:752px;top:1652px">- Client Name</div>

<!-- Call to action -->
<div class="abs cta-photo" role="img" aria-label="Blue-tinted photo of a drone pilot preparing equipment in a field"></div>
<svg class="abs" style="left:0;top:1930px" width="1200" height="90" viewBox="0 1930 1200 90" aria-hidden="true">
  <path d="M0 1932 Q600 2094 1200 1932 L1200 2020 L0 2020 Z" fill="#fff"/>
</svg>
<h2 class="abs cta-title">Lorem Ipsum is simply dummy text of the printing.</h2>
<div class="abs cta-button">CONTACT US</div>

<!-- Contact -->
<h2 class="abs section-title" style="top:2054px">Contact Us</h2>
<div class="abs field field-name">Name</div>
<div class="abs field field-email">Email Id</div>
<div class="abs field field-message">Message</div>
<div class="abs send">
  <svg width="28" height="24" viewBox="0 0 28 24" fill="none" stroke="#fff" stroke-width="2"><path d="M26 2L2 11l9 3 2 8 4-6 6 4z"/><path d="M11 14L26 2"/></svg>
  SEND
</div>

<div class="abs info" style="top:2133px">
  <svg width="18" height="22" viewBox="0 0 18 22" fill="var(--blue)"><path d="M9 0a8 8 0 018 8c0 6-8 14-8 14S1 14 1 8a8 8 0 018-8zm0 5a3 3 0 100 6 3 3 0 000-6z"/></svg>
  <span>Lorem Ipsum is simply dummy<br>text of the printing.</span>
</div>
<div class="abs info" style="top:2196px">
  <svg width="20" height="20" viewBox="0 0 20 20" fill="var(--blue)"><path d="M4 1l4 4-2 3q2 4 6 6l3-2 4 4-3 3Q8 18 1 4z"/></svg>
  <span>615-382-9041</span>
</div>
<div class="abs info" style="top:2234px">
  <svg width="20" height="16" viewBox="0 0 20 16" fill="none" stroke="var(--blue)" stroke-width="2"><rect x="1" y="1" width="18" height="14"/><path d="M1 2l9 7 9-7"/></svg>
  <span>office@pelhamdronesolutions-example.com</span>
</div>

<footer class="abs footer">&copy;PELHAM DRONE SOLUTIONS - 2017. All Rights Reserved.</footer>

</body>
</html>
```